House-share and Room Rental Website (With Focus on the Bedroom Landing Page)

Looking for website design for our House-share (executive accommodation) and room rental business.

Our company name is: Lodgivo could also be written as LodGivo or lodgivo. Either is fine .. just looking for a nice clean catchy logo to go with the design.

EXAMPLES
These are examples of other websites in this field that are doing well. this is a kind of baseline.
https://nestpartners-example.com.au/
https://www.bunkora-example.com/
https://www.dwelzy-example.com/
https://www.habiquo-example.net/
https://www.cohabiscout-example.com.au/

Our business model is to rent rooms to people looking for high-quality accommodation. We fill the gap between those looking to rent rooms and those with rooms to rent. However, our model is slightly different from those already on the market as we looking to fill a massive gap in the market delivering upmarket rooms for rent.(Executive Accommodation) also in the back end will be coupled with a self management process in the back end.

We offer executive style accommodation that stands out above the rest. With special extras like fire safety.. and management processes that create happier homes. We are looking for a web design package that can help us grow and scale our business. We need a design that is captivating

Our MAIN focus is having a room landing page that stands out from the rest... The core of our business will rely on the promotion of the rooms in a share house... so the whole design relies on the BEDROOM landing page to drive results.

Target Market(s)

We have 2 markets we are aiming at ... the first market is people offering rooms to rent who want the highest rental return. The second market is people looking to rent safe, high-quality rooms, in houses that are well managed and looked after.

Industry/Entity Type

Share Economy

Logo Text

LodGivo

Number of Pages Required

5+ page

Font styles to use
Sans Serif

Colors
3276b5

Requirements
Must have
• A messaging system whereby we can create direct communication between those offering rooms and those looking for rooms.
• A call to action that says " Schedule an Inspection"
• Landing page for promoting rooms
• A home page for showing stock.
• Profile page for those selling rooms
• Profile page for those looking for rooms.
• A scheduling calendar for booking inspections
Nice to have
• Pages where new residents can lock in a room.. pay bond and rents.. and sign contracts
• Notifications
• SMS capabilities in the backend.
Should not have
• No script or handwriting fonts.

```html
<!DOCTYPE html>
<html lang="en">
<head>
<meta charset="utf-8">
<title>Lodgivo — Bedroom</title>
<link href="https://fonts.googleapis.com/css2?family=Barlow:wght@400;500&display=swap" rel="stylesheet">
<style>
:root{
  --brand:#3276b5;
  --ink:#222;
  --text:#444;
  --muted:#555;
  --rule:#e2e2e2;
  --bg:#fff;
  --icon:#4a6f96;
}
*{box-sizing:border-box;margin:0;padding:0}
html,body{width:801px;height:1200px;overflow:hidden;background:var(--bg)}
body{position:relative;font-family:'Barlow',sans-serif;color:var(--ink)}
.abs{position:absolute}
.logo{font-size:19px;color:var(--brand);font-weight:400;top:16px;left:115px;display:flex;align-items:center;gap:5px}
.logo .mark{width:8px;height:8px;background:var(--brand);display:inline-block}
.nav{top:22px;left:334px;font-size:10.5px;color:var(--text)}
.nav span{position:absolute;white-space:nowrap}
.cta{top:16px;left:578px;width:107px;height:22px;border:1.2px solid #333;border-radius:12px;font-size:8px;display:flex;align-items:center;justify-content:center;color:#222}
.hero{top:46px;left:0;width:801px;height:318px;background:linear-gradient(180deg,#b9b2a6 0%,#c8c1b4 40%,#9c9aa0 70%,#8e8b88 100%)}
.thumbs{top:369px;left:0;display:flex;gap:5.3px}
.thumbs div{width:66px;height:57px;flex:none}
h1{top:466px;left:115px;font-size:18px;font-weight:400;letter-spacing:.3px}
.specs{top:500px;left:115px;width:180px;font-size:9.8px}
.specs .row{height:26px;display:flex;align-items:center;border-bottom:1px solid var(--rule);width:180px}
.specs .row:last-child{border-bottom:none}
.specs .k{width:91px;color:#222}
.specs .v{color:var(--text);white-space:nowrap}
.addr-h{top:775px;left:115px;font-size:13px;display:flex;align-items:center;gap:3px}
.addr{top:796px;left:115px;font-size:8.6px;line-height:14.5px;color:#333}
.price{top:836px;left:116px;font-size:12.5px;display:flex}
.price .v{margin-left:43px;color:var(--brand);font-weight:500;font-size:13px}
.util{top:862px;left:116px;font-size:9.8px;display:flex}
.util .v{margin-left:59px;color:var(--text)}
h2{font-size:12px;font-weight:400}
.amen{font-size:8.6px;color:#333;display:flex;align-items:center;gap:7px;line-height:10.5px}
.amen svg{width:27px;height:24px;flex:none}
.transport{top:684px;left:379px;font-size:8.6px;color:#333;display:flex;align-items:center;gap:10px}
.map{top:742px;left:379px;width:307px;height:156px;background:linear-gradient(135deg,#dfe9d6,#cfe1c2 50%,#e6e7df)}
.foot-line{left:115px;width:571px;height:1px;background:var(--rule)}
.foot-logo{top:962px;left:115px;font-size:17px;color:#222;display:flex;align-items:center;gap:5px}
.foot-logo .mark{width:7px;height:7px;background:#222;display:inline-block}
.social{top:965px;left:608px;display:flex;gap:4px}
.social i{width:16px;height:16px;border-radius:50%;display:block}
.col h3{font-size:9.5px;font-weight:400;color:#222;margin-bottom:10px}
.col p{font-size:7.3px;color:#444;line-height:12.5px}
.copy{top:1168px;left:0;width:801px;text-align:center;font-size:8px;color:#333}
</style>
</head>
<body>
<div class="abs logo"><span class="mark"></span>Lodgivo</div>
<nav class="abs nav">
  <span style="left:0">Home</span><span style="left:48px">About</span><span style="left:96px">Rooms</span><span style="left:148px">News</span><span style="left:194px">Contact</span>
</nav>
<div class="abs cta">Schedule an Inspection</div>

<div class="abs hero" role="img" aria-label="Photo of a furnished bedroom with a tufted bed, bench and bedside lamps"></div>
<div class="abs thumbs" role="img" aria-label="Gallery of room and house photos">
  <div style="background:#8a8f96"></div><div style="background:#d8cfc8"></div><div style="background:#9a8a80"></div><div style="background:#b09a80"></div><div style="background:#c9c2bb"></div><div style="background:#d2cdc6"></div><div style="background:#6e6258"></div><div style="background:#8a8a74"></div><div style="background:#7fa4c9"></div><div style="background:#8a5a36"></div><div style="background:#cfcfcf"></div><div style="background:#5c6470"></div>
</div>

<h1 class="abs">BEDROOM NAME</h1>
<div class="abs specs">
  <div class="row"><span class="k">Gender Preference</span><span class="v">: Male</span></div>
  <div class="row"><span class="k">Size of room</span><span class="v">: 1200Sqm</span></div>
  <div class="row"><span class="k">Bathroom</span><span class="v">: Private</span></div>
  <div class="row"><span class="k">Parking</span><span class="v">: Private</span></div>
  <div class="row"><span class="k">Smoking</span><span class="v">: Male</span></div>
  <div class="row"><span class="k">Minimum contract</span><span class="v">: Usually 3 months</span></div>
  <div class="row"><span class="k">Bed size</span><span class="v">: 12X12</span></div>
  <div class="row"><span class="k">Type of housemates</span><span class="v">: Professionals</span></div>
  <div class="row"><span class="k">Room type</span><span class="v">: Private</span></div>
  <div class="row"><span class="k">Internet speed</span><span class="v">: 180 kbps</span></div>
</div>

<div class="abs addr-h"><svg width="9" height="11" viewBox="0 0 9 11"><path d="M4.5 0.5a3.6 3.6 0 0 0-3.6 3.6c0 2.7 3.6 6.4 3.6 6.4s3.6-3.7 3.6-6.4A3.6 3.6 0 0 0 4.5.5z" fill="#222"/><circle cx="4.5" cy="4.1" r="1.3" fill="#fff"/></svg>Adress</div>
<div class="abs addr">Lorem isom 22 Prestige Circle<br>Harlow, TX.75910 dummy</div>
<div class="abs price"><span>Rental price</span><span class="v">: $250.00</span></div>
<div class="abs util"><span>Utilities</span><span class="v">: Included</span></div>

<h2 class="abs" style="top:469px;left:378px">ROOM Amenities</h2>
<svg width="0" height="0" style="position:absolute"><defs>
  <symbol id="box" viewBox="0 0 27 24"><rect x="0.5" y="0.5" width="26" height="23" fill="none" stroke="#9aa" stroke-width="1"/></symbol>
</defs></svg>
<div class="abs amen" style="top:509px;left:378px"><svg viewBox="0 0 27 24"><use href="#box"/><path d="M9 6h9v6H9zM8 12h11M11 12v7M16 12v7M10 19h7" fill="none" stroke="var(--icon)"/></svg>Furnished/<br>unfurnished</div>
<div class="abs amen" style="top:509px;left:504px"><svg viewBox="0 0 27 24"><use href="#box"/><path d="M6 6h15v10H6zM11 19h5M13.5 16v3" fill="none" stroke="var(--icon)"/></svg>TV</div>
<div class="abs amen" style="top:509px;left:598px"><svg viewBox="0 0 27 24"><use href="#box"/><path d="M7 5l13 14M20 5L7 19M18 5v5" fill="none" stroke="var(--icon)"/></svg>Kitchenette</div>
<div class="abs amen" style="top:549px;left:378px"><svg viewBox="0 0 27 24"><use href="#box"/><path d="M5 12h17M7 12v7M20 12v7M14 12v5h6M9 6h6v4H9z" fill="none" stroke="var(--icon)"/></svg>Study Desk /<br>&nbsp;Workstation</div>
<div class="abs amen" style="top:549px;left:504px"><svg viewBox="0 0 27 24"><use href="#box"/><path d="M6 4h15v16H6zM13.5 4v16M6 11h7M15 8h4" fill="none" stroke="var(--icon)"/></svg>Wardrobe</div>
<div class="abs amen" style="top:549px;left:598px"><svg viewBox="0 0 27 24"><use href="#box"/><path d="M8 19V8a4 4 0 0 1 8 0M13 9h6l-3 3zM15 14v2M18 14v2M17 17v2" fill="none" stroke="var(--icon)"/></svg>Ensuite shower</div>
<div class="abs amen" style="top:589px;left:378px"><svg viewBox="0 0 27 24"><use href="#box"/><path d="M5 6h17v12H5zM5 10h17M5 14h17" fill="none" stroke="var(--icon)"/></svg>Storage space</div>

<h2 class="abs" style="top:644px;left:379px">Public amenities..</h2>
<div class="abs transport">Transport Options
  <svg width="72" height="22" viewBox="0 0 72 22" fill="none" stroke="#667" stroke-width="1">
    <rect x="2" y="2" width="15" height="14" rx="2"/><path d="M2 9h15M5 16l-3 5M14 16l3 5"/>
    <rect x="27" y="2" width="14" height="16" rx="2"/><path d="M27 10h14M29 18v2M39 18v2"/>
    <path d="M51 15v-5l3-5h12l3 5v5zM51 10h18M53 15v3M67 15v3" stroke="var(--icon)"/>
  </svg>
</div>
<div class="abs" style="top:721px;left:379px;font-size:8.6px;color:#333">Location or distance to the city- 120 km</div>
<div class="abs map" role="img" aria-label="Map showing the room's location and route to the city"></div>

<div class="abs foot-line" style="top:940px;left:0;width:801px"></div>
<div class="abs foot-logo"><span class="mark"></span>Lodgivo</div>
<div class="abs social"><i style="background:#2d4f8e"></i><i style="background:#2aa3ef"></i><i style="background:#1b6fa8"></i><i style="background:#e23a2e"></i></div>
<div class="abs foot-line" style="top:1001px"></div>

<div class="abs col" style="top:1017px;left:115px"><h3>Room amenities</h3><p>Furnished/unfurnished<br>TV<br>Storage space<br>Study Desk / Workstation<br>Wardrobe<br>Ensuite shower<br>Kitchenette</p></div>
<div class="abs col" style="top:1017px;left:293px"><h3>Rooms</h3><p>Lorem ipsum dolo<br>Consectetur adipiscing elit.<br>Fusce eget leo tincid<br>Donec consequat<br>Praesent elementum<br>Jmauris posueret<br>Aenean a ex eu lectu</p></div>
<div class="abs col" style="top:1017px;left:433px"><h3>&nbsp;</h3><p>Lorem ipsum dolo<br>Consectetur adipiscing elit.<br>Fusce eget leo tincid<br>Donec consequat<br>Praesent elementum<br>Jmauris posueret<br>Aenean a ex eu lectu</p></div>
<div class="abs col" style="top:1017px;left:590px"><h3>Other Links</h3><p>Lorem ipsum dolo<br>Consectetur adipiscing elit.<br>Fusce eget leo tincid<br>Donec consequat<br>Praesent elementum<br>Jmauris posueret<br>Aenean a ex eu lectu</p></div>

<div class="abs foot-line" style="top:1151px"></div>
<div class="abs copy">Copyright 2019 Lodgivo. All Rights Reserved</div>
</body>
</html>
```